Web Design Project

We are an IT System Integrator. We provide Korvin 450 ERP System, CRM etc. We also provide hardware, networking servicing. Please look at www.zolvantix.com.sg. They provide the same service as us. We like to redesign our web site. I will attached the color that I prefer for reference.

Our website is www.tadurk.com.sg.  It has been created about 14 years ago.  We are trying to revamp it with a new look and information.   The new website must be informative, fast.    I have attached an attachment which show the color that I prefer(brownish golden).   

Our competitor (www.zolvantix.com) is carrying the same trade as us.  They have all the informations In their website that we will like to have.  Therefore I recommend you to take a look at my competitor website and have a better   
understanding on the kind of information I would like to have for my new website.

This project is guarantee to the person with the best design.  We can have it guarantee.

Target Market(s)

Corporate and companies

Industry/Entity Type

Hardware

```html
<!DOCTYPE html>
<html lang="en">
<head>
<meta charset="utf-8">
<title>Tadurk Information Systems Pte Ltd</title>
<link rel="stylesheet" href="https://fonts.googleapis.com/css2?family=Ubuntu:wght@400;500;700&family=Gelasio:ital,wght@0,700;1,400&family=Arimo:wght@400;700&display=swap">
<style>
:root{
  --top-blue:#129be0;
  --nav-text:#555;
  --gold:#a6702a;
  --gold-dark:#6f4512;
  --title:#3b3a9c;
  --body:#777;
  --hero-top:#c8dcf0;
  --hero-bottom:#d9ecf9;
  --footer:#0f3e5a;
  --footer-line:#2a5873;
  --base:#111;
}
*{margin:0;padding:0;box-sizing:border-box}
html,body{width:1034px;height:1200px;overflow:hidden;background:#fff}
.page{position:relative;width:1034px;height:1200px;overflow:hidden;font-family:Arimo,sans-serif}
.abs{position:absolute}
.top-bar{left:0;top:0;width:1034px;height:4px;background:var(--top-blue)}
.brand{left:110px;top:12px;display:flex;align-items:center;gap:14px}
.brand-mark{width:108px;height:76px;display:flex;align-items:center;justify-content:center}
.brand-name{font-family:Ubuntu,sans-serif;font-weight:500;color:var(--gold);font-size:11.5px;line-height:23px;letter-spacing:.5px}
.main-nav{left:412px;top:4px;display:flex;height:41px;font-family:Ubuntu,sans-serif;font-size:11.5px;color:var(--nav-text)}
.main-nav a{display:flex;align-items:center;padding:0 12px;border-right:1px solid #e6e6e6;text-decoration:none;color:inherit}
.main-nav a:last-child{border-right:0}
.main-nav a.active{background:linear-gradient(#3c9ee6,#2480cc);color:#fff;font-weight:500;padding:14px 10px 0;align-items:flex-start}
.sub-nav{right:113px;top:85px;font-size:9px;color:#888;letter-spacing:.2px}
.sub-nav span{margin:0 11px}
.header-rule{left:0;top:105px;width:1034px;height:3px;background:#eee}
.hero{left:0;top:108px;width:1034px;height:340px;background:linear-gradient(var(--hero-top),var(--hero-bottom))}
.hero-photo{left:80px;top:118px;width:420px;height:300px;background:radial-gradient(ellipse 55% 60% at 50% 55%,rgba(95,100,115,.55),rgba(140,150,170,.3) 55%,rgba(205,222,240,0) 100%)}
.quote{left:548px;top:150px;width:380px;font-family:Gelasio,serif;font-style:italic;font-size:20px;line-height:36px;color:#38389c}
.learn-btn{left:546px;top:301px;width:124px;height:33px;border-radius:4px;background:linear-gradient(#28a2e8,#0f6fc2);color:#fff;font-family:Gelasio,serif;font-size:17px;display:flex;align-items:center;justify-content:center}
.dots{left:565px;top:374px;display:flex;gap:6px}
.dots i{width:8px;height:8px;border-radius:50%;background:#555}
.dots i:first-child{background:#1f7fd1;box-shadow:0 0 0 2px #9ccdf1}
.waves{left:0;top:385px}
.services{left:0;top:448px;width:1034px;height:516px;background:linear-gradient(#f1f1f1,#f8f8f8 60%,#f4f4f4)}
.svc{display:flex;gap:12px;width:290px}
.svc-icon{flex:none;width:66px;height:66px;border-radius:50%;background:radial-gradient(circle at 40% 35%,#d39a52,var(--gold) 55%,var(--gold-dark));display:flex;align-items:center;justify-content:center;box-shadow:0 2px 3px rgba(0,0,0,.25)}
.svc h3{font-family:Ubuntu,sans-serif;font-weight:400;font-size:12.5px;color:var(--title);line-height:14px;margin-top:16px;margin-bottom:2px}
.svc p{font-size:10.5px;color:var(--body);line-height:12.5px}
.arrow{width:29px;height:29px;border-radius:50%;border:1.5px solid #2a8fd6;background:#fff}
.section-title{font-family:Ubuntu,sans-serif;font-weight:500;font-size:15px;color:var(--title)}
.welcome-photo{left:116px;top:688px;width:246px;height:93px;border:1px solid #ccc;background:linear-gradient(90deg,#cfe2ef,#8fb9d6 50%,#2d7eb3)}
.welcome-text{left:118px;top:797px;width:348px;font-size:10.5px;color:#666;line-height:16px}
.read-more{left:403px;top:915px;font-size:10.5px;color:#2a7fc5;text-decoration:underline}
.clients{left:484px;top:687px;width:440px;height:248px;background:#fff;border:1px solid #ccc;display:grid;grid-template-columns:repeat(4,1fr);grid-template-rows:repeat(3,1fr);align-items:center;justify-items:center;padding:8px}
.client{font-family:Ubuntu,sans-serif;font-weight:700;font-size:14px;color:var(--title);text-align:center}
.footer{left:0;top:964px;width:1034px;height:196px;background:var(--footer);color:#fff}
.footer h4{position:absolute;font-family:Gelasio,serif;font-weight:700;font-size:14px;top:26px}
.divider{position:absolute;top:38px;width:1px;height:135px;background:var(--footer-line)}
.links{position:absolute;left:130px;top:56px;font-size:10.5px;line-height:19.3px;list-style:none}
.contact{position:absolute;left:277px;top:54px;font-size:10px;line-height:13.5px}
.contact-row{position:absolute;left:277px;display:flex;align-items:center;gap:14px;font-size:12px;font-weight:700}
.testimonial{position:absolute;left:534px;top:58px;width:160px;font-size:10px;font-style:italic;line-height:15px}
.testimonial .by{position:absolute;left:70px;top:86px;font-style:normal;font-weight:700;font-size:9.5px;white-space:nowrap}
.social{position:absolute;left:767px;top:56px;display:flex;gap:12px}
.social span{display:flex;flex-direction:column;align-items:center;font-size:8px;gap:2px}
.social i{width:25px;height:24px;background:#2c7bc4;border-radius:2px}
.copyright{left:0;top:1160px;width:1034px;height:40px;background:var(--base);color:#ddd;font-size:10.5px;display:flex;align-items:center;justify-content:center}
</style>
</head>
<body>
<div class="page">
  <div class="abs top-bar"></div>

  <div class="abs brand">
    <div class="brand-mark"><svg width="60" height="60"><circle cx="30" cy="30" r="28" fill="#c89447"/></svg></div>
    <div class="brand-name">TADURK<br>INFORMATION<br>SYSTEMS PTE LTD</div>
  </div>

  <nav class="abs main-nav">
    <a class="active">COMPANY</a><a>PRODUCTS</a><a>LEDGRA</a><a>SERVICES</a><a>CLIENTELE</a><a>CAREERS</a><a>INFOBIN</a>
  </nav>
  <div class="abs sub-nav">HOME<span>|</span>SITEMAP<span>|</span>LOG INCIDENT<span>|</span>ENQUIRY<span>|</span>CONTACT<span>|</span>CLIENT SUPPORT</div>
  <div class="abs header-rule"></div>

  <section class="abs hero"></section>
  <div class="abs hero-photo" role="img" aria-label="Four smiling business professionals standing before a silver jigsaw globe"></div>
  <p class="abs quote">"To win and retain the confidence and loyalty of customers through dedication to quality and excellence in work."</p>
  <div class="abs learn-btn">Learn more</div>
  <div class="abs dots"><i></i><i></i><i></i></div>
  <svg class="abs waves" width="1034" height="70" viewBox="0 0 1034 70">
    <path d="M0 35 C120 0 230 -5 380 25 S760 55 1034 10 L1034 20 C800 60 520 70 360 40 S120 15 0 45Z" fill="#0a74cf"/>
    <path d="M30 42 C120 25 220 28 292 40 C220 33 120 33 30 45Z" fill="#0b2478"/>
    <path d="M530 28 C700 36 900 22 1030 10 C900 30 700 45 530 32Z" fill="#0b2478"/>
    <path d="M0 60 L1034 60 L1034 70 L0 70Z" fill="#f1f1f1"/>
    <path d="M0 46 C150 20 260 25 380 42 S780 62 1034 22 L1034 62 L0 62Z" fill="#f1f1f1"/>
  </svg>

  <section class="abs services"></section>
  <div class="abs arrow" style="left:66px;top:525px"><svg width="26" height="26"><path d="M15 7l-6 6 6 6" stroke="#2a8fd6" stroke-width="2" fill="none"/></svg></div>
  <div class="abs arrow" style="left:936px;top:525px"><svg width="26" height="26"><path d="M11 7l6 6-6 6" stroke="#2a8fd6" stroke-width="2" fill="none"/></svg></div>

  <div class="abs svc" style="left:108px;top:460px">
    <div class="svc-icon"><svg width="34" height="36"><ellipse cx="17" cy="6" rx="15" ry="5" fill="#fff"/><rect x="2" y="8" width="30" height="8" fill="#fff"/><rect x="2" y="18" width="30" height="7" fill="#fff"/><rect x="2" y="27" width="30" height="7" rx="3" fill="#fff"/></svg></div>
    <div><h3>Corvane Software and Technology Reseller</h3><p>Lorem ipsum dolor sit amet, onsectuer</p></div>
  </div>
  <div class="abs svc" style="left:389px;top:460px">
    <div class="svc-icon"><svg width="34" height="34"><path d="M6 15a11 11 0 0 1 20-5" stroke="#fff" stroke-width="5" fill="none"/><path d="M28 4v9h-9z" fill="#fff"/><path d="M28 19a11 11 0 0 1-20 5" stroke="#fff" stroke-width="5" fill="none"/><path d="M6 30v-9h9z" fill="#fff"/></svg></div>
    <div><h3>Migrations &amp; Upgrades to the 9's</h3><p>Lorem ipsum dolor sit amet,<br>onsectetuer adipiscing elit, sed diam<br>nonummy</p></div>
  </div>
  <div class="abs svc" style="left:676px;top:455px">
    <div class="svc-icon" style="margin-top:5px"><svg width="34" height="34"><rect x="2" y="2" width="30" height="30" fill="#fff"/><path d="M6 9h22M6 15h22M6 21h14" stroke="#6aa0c8" stroke-width="1.5"/><path d="M11 20l6 7 13-18" stroke="#6cbf2a" stroke-width="4" fill="none"/></svg></div>
    <div><h3>Report Development</h3><p>Lorem ipsum dolor sit amet,<br>onsectetuer adipiscing elit, sed diam<br>nonummy</p></div>
  </div>

  <div class="abs svc" style="left:108px;top:554px">
    <div class="svc-icon"><svg width="36" height="32"><circle cx="12" cy="8" r="6" fill="#fff"/><path d="M1 30c0-9 4-14 11-14s11 5 11 14z" fill="#fff"/><circle cx="26" cy="14" r="5" fill="#fff"/><path d="M18 30c0-7 3-11 8-11s9 4 9 11z" fill="#fff"/></svg></div>
    <div><h3>Consulting Services for Brightel®<br>and Scopeline®</h3><p>Lorem ipsum dolor sit amet, onsectuer</p></div>
  </div>
  <div class="abs svc" style="left:389px;top:554px">
    <div class="svc-icon"><svg width="30" height="34"><path d="M3 2h15l8 8v22H3z" fill="none" stroke="#fff" stroke-width="3"/><path d="M20 22h9M24.5 17.5v9" stroke="#fff" stroke-width="3"/></svg></div>
    <div><h3>Custom Applications Development</h3><p>Lorem ipsum dolor sit amet,<br>onsectetuer adipiscing elit, sed diam<br>nonummy</p></div>
  </div>
  <div class="abs svc" style="left:676px;top:554px">
    <div class="svc-icon"><svg width="34" height="34"><path d="M7 5a7 7 0 0 0 8 9l14 14-3 3-14-14a7 7 0 0 1-9-8l4 4 4-1 1-4z" fill="#fff"/></svg></div>
    <div><h3>Technical and CNC</h3><p>Lorem ipsum dolor sit amet,<br>onsectetuer adipiscing elit, sed diam<br>nonummy</p></div>
  </div>

  <h2 class="abs section-title" style="left:114px;top:655px">Welcome to Tadurk Information Systems Pte Ltd</h2>
  <h2 class="abs section-title" style="left:487px;top:655px">OUR CLIENTS</h2>

  <div class="abs welcome-photo" role="img" aria-label="Businesswoman beside blue jigsaw globe pieces"></div>
  <p class="abs welcome-text">Lorem ipsum dolor sit amet, consectetuer adipiscing elit, sed diam nonummy nibh euismod tincidunt ut laoreet dolore magna aliquam erat volutpat. Ut wisi enim ad minim veniam, quis nostrud exerci tation ullamcorper suscipit lobortis nisl ut aliquip ex ea commodo consequat. Duis autem vel eum iriure dolor in hendrerit in vulputate velit esse molestie consequat, vel illum dolore eu feugiat nulla facilisis at vero eros et accumsan et iusto odio dignissim qui blandit praesent luptatum.</p>
  <a class="abs read-more">Read More</a>

  <div class="abs clients">
    <div class="client">Harvestine<br>Dairy</div>
    <div class="client">Morvale</div>
    <div class="client">Avrex</div>
    <div class="client" style="grid-row:1/3;grid-column:4">KRB</div>
    <div class="client">Civic<br>Creamery</div>
    <div class="client">Pellham Dairy</div>
    <div class="client">Nuvia</div>
    <div class="client">Orlen Farms</div>
    <div class="client">Hollis Dairy</div>
    <div class="client">Fieldmark</div>
  </div>

  <footer class="abs footer">
    <h4 style="left:125px">Quick Links</h4>
    <h4 style="left:275px">Contact Details</h4>
    <h4 style="left:531px">Client's Testimonial</h4>
    <h4 style="left:767px">Follow Us</h4>
    <div class="divider" style="left:239px"></div>
    <div class="divider" style="left:487px"></div>
    <div class="divider" style="left:725px"></div>
    <ul class="links"><li>Company</li><li>Products</li><li>LEDGRA</li><li>Services</li><li>Clientele</li><li>Careers</li><li>Infobin</li></ul>
    <p class="contact">58 Lorong Tembusu<br>#05-11 Quarry Point<br>Singapore 418902</p>
    <div class="contact-row" style="top:104px"><svg width="16" height="16"><path d="M3 1l4 0 1 4-2 2c1 2 3 4 5 5l2-2 4 1v4l-2 1C8 15 1 8 1 3z" fill="#fff"/></svg><span>(065) 6410-3857</span></div>
    <div class="contact-row" style="top:128px;gap:10px"><svg width="18" height="13"><rect x="1" y="1" width="16" height="11" fill="none" stroke="#fff" stroke-width="1.5"/><path d="M1 1l8 6 8-6" stroke="#fff" stroke-width="1.5" fill="none"/></svg><span>sales@tadurk.com.sg</span></div>
    <div class="testimonial"><span style="position:absolute;left:-14px;top:-6px;font-size:20px;font-family:Gelasio,serif">“</span>Lorem ipsum dolor sit amet, consectetuer adipiscing elit, sed diam nonummy nibh euismod tincidunt ut laoreet dolore magna aliquam erat volutpat. <span style="font-size:16px;font-family:Gelasio,serif">”</span><span class="by">- DALEN MORROW</span></div>
    <div class="social"><span><i></i>Fanlo</span><span><i></i>Chirpa</span><span><i></i>Linkra</span></div>
  </footer>
  <div class="abs copyright">© Copyrights 2013. Tadurk Information Systems. All Rights Reserved.</div>
</div>
</body>
</html>
```